Business Card Design

We need a business card design for a Dry cleaners in Brisbane, Australia. We are trying to promote a fresh/clean image consistent with our website. www.pinnelgarmentcare.com.au

Looking for a professional neat card that's easy to read.

Target Market(s)

Customers looking for a professional, fresh and clean drycleaners.

Industry/Entity Type

Business

Contact Information for Business Card

See our existing business card. The Fax number (07) 3468 5270 to be removed.

Requirements
Must have
• All the details on current business card less the fax number.
Nice to have
• I like white text on coloured background. Blue works well as we are located near the water...

```html
<!DOCTYPE html>
<html lang="en">
<head>
<meta charset="utf-8">
<title>Pinnel Garment Care – Business Card</title>
<link href="https://fonts.googleapis.com/css2?family=Open+Sans:wght@400;600;700&family=Oswald:wght@500&display=swap" rel="stylesheet">
<style>
  :root{
    --bg:#e9e7e3;
    --card:#ffffff;
    --blue:#2e3a97;
    --red:#e8323c;
    --ink:#333846;
    --muted:#6a6f7c;
  }
  *{box-sizing:border-box;margin:0;padding:0}
  html,body{width:1200px;height:682px;overflow:hidden}
  body{background:var(--bg);font-family:"Open Sans",Arial,sans-serif;display:flex;align-items:center;justify-content:center}
  .card{position:relative;width:900px;height:514px;background:var(--card);box-shadow:0 10px 30px rgba(0,0,0,.18);overflow:hidden}
  .top-stripe{position:absolute;left:0;top:0;width:100%;height:16px;background:var(--blue)}
  .brand{position:absolute;left:62px;top:118px;font-weight:700;font-size:50px;line-height:1;color:var(--blue);letter-spacing:.5px;white-space:nowrap}
  .brand-dot{display:inline-block;width:22px;height:22px;border-radius:50%;background:var(--red);margin-right:14px;vertical-align:middle}
  .id-icon{position:absolute;left:62px;top:258px;width:54px;height:54px;background:var(--blue);display:flex;align-items:center;justify-content:center}
  .id-icon-accent{position:absolute;left:62px;top:318px;width:54px;height:12px;background:var(--red)}
  .name-band{position:absolute;left:124px;top:258px;width:318px;height:54px;background:var(--blue);color:#fff;font-family:"Oswald",Arial,sans-serif;font-weight:500;font-size:30px;letter-spacing:3px;display:flex;align-items:center;padding-left:24px;white-space:nowrap}
  .title-band{position:absolute;left:560px;top:258px;right:0;height:54px;background:var(--blue);color:#fff;font-weight:600;font-size:19px;letter-spacing:2.5px;display:flex;align-items:center;padding-left:28px;white-space:nowrap}
  .title-accent{position:absolute;left:560px;top:326px;right:0;height:14px;background:var(--red)}
  .contacts{position:absolute;left:124px;top:360px;display:grid;grid-template-columns:300px 340px;row-gap:14px;column-gap:20px}
  .contact{display:flex;align-items:center;gap:12px;font-size:17px;color:var(--ink);white-space:nowrap}
  .contact svg{flex:none;width:20px;height:20px}
  .address-band{position:absolute;left:0;right:0;top:448px;height:46px;background:var(--red);color:#fff;font-size:17px;font-weight:600;display:flex;align-items:center;padding-left:62px;gap:12px;white-space:nowrap}
</style>
</head>
<body>
  <div class="card">
    <div class="top-stripe"></div>

    <div class="brand"><span class="brand-dot"></span>Pinnel Garment Care</div>

    <div class="id-icon">
      <svg width="30" height="30" viewBox="0 0 24 24" fill="#fff" aria-hidden="true">
        <circle cx="12" cy="8" r="4.5"/>
        <path d="M3 22c0-5 4-8 9-8s9 3 9 8z"/>
      </svg>
    </div>
    <div class="id-icon-accent"></div>
    <div class="name-band">DANIEL HART</div>

    <div class="title-band">GENERAL MANAGER</div>
    <div class="title-accent"></div>

    <div class="contacts">
      <div class="contact">
        <svg viewBox="0 0 24 24" fill="none" stroke="var(--ink)" stroke-width="2" aria-hidden="true"><path d="M5 3h4l2 5-2.5 1.5a11 11 0 0 0 6 6L16 13l5 2v4a2 2 0 0 1-2 2A17 17 0 0 1 3 5a2 2 0 0 1 2-2z"/></svg>
        (07) 3219 4406
      </div>
      <div class="contact">
        <svg viewBox="0 0 24 24" fill="none" stroke="var(--ink)" stroke-width="2" aria-hidden="true"><rect x="3" y="5" width="18" height="14" rx="1"/><path d="M3 6l9 7 9-7"/></svg>
        hello@pinnelgarmentcare.com.au
      </div>
      <div class="contact">
        <svg viewBox="0 0 24 24" fill="none" stroke="var(--ink)" stroke-width="2" aria-hidden="true"><rect x="6" y="2" width="12" height="20" rx="2"/><path d="M10 18h4"/></svg>
        0412 608 334
      </div>
      <div class="contact">
        <svg viewBox="0 0 24 24" fill="none" stroke="var(--ink)" stroke-width="2" aria-hidden="true"><circle cx="12" cy="12" r="9"/><path d="M3 12h18M12 3c3 3 3 15 0 18M12 3c-3 3-3 15 0 18"/></svg>
        www.pinnelgarmentcare.com.au
      </div>
    </div>

    <div class="address-band">
      <svg width="18" height="22" viewBox="0 0 24 30" fill="#fff" aria-hidden="true"><path d="M12 0a10 10 0 0 0-10 10c0 8 10 20 10 20s10-12 10-20A10 10 0 0 0 12 0zm0 14a4 4 0 1 1 0-8 4 4 0 0 1 0 8z"/></svg>
      14 Wharf Street, Brisbane QLD 4000
    </div>
  </div>
</body>
</html>
```